Freelance Translator in Need of a Business Card

I am a freelance Japanese to English translator. I work in the video game localization industry and do literary translation in my spare time. I would like to have both the English word 'Translator' and the Japanese '翻訳者' in the job title. The final design should evoke trust, openness, and reliability.

Target Market(s)

Video game localization companies
Japanese comic book artists

Industry/Entity Type

Business

Contact Information for Business Card

Daniel Forsvik, Translator
dan.forsvik@quellmail.net
torvenwords.com
twitter: @torven_wd

Colors

Designer to choose colors to be used in the design.

```html
<!DOCTYPE html>
<html lang="en">
<head>
<meta charset="utf-8">
<title>Torven Words — Business Card</title>
<link rel="stylesheet" href="https://fonts.googleapis.com/css2?family=Bodoni+Moda:ital,wght@0,400;0,700;0,800&family=Noto+Serif+JP:wght@400&display=swap">
<style>
  :root {
    --stage: #e9e6e1;
    --card-black: #151515;
    --card-white: #f2f2f2;
    --ink-white: #ffffff;
    --accent-orange: #e89a35;
    --ink-black: #111111;
  }
  * { margin: 0; padding: 0; box-sizing: border-box; }
  html, body {
    width: 1200px;
    height: 892px;
    overflow: hidden;
    background: var(--stage);
  }
  .stage {
    position: relative;
    width: 1200px;
    height: 892px;
    display: flex;
    justify-content: center;
    align-items: center;
    gap: 80px;
  }
  .card {
    position: relative;
    width: 340px;
    height: 595px;
    background: var(--card-black);
    overflow: hidden;
    box-shadow: 0 10px 30px rgba(0,0,0,0.18);
  }
  /* Front */
  .card-front { color: var(--ink-white); font-family: "Bodoni Moda", "Didot", serif; }
  .brand-name {
    position: absolute;
    top: 58px;
    left: 0;
    right: 0;
    text-align: center;
    font-size: 38px;
    font-weight: 800;
    letter-spacing: 0.5px;
  }
  .person {
    position: absolute;
    top: 178px;
    left: 0;
    right: 0;
    text-align: center;
  }
  .person-name {
    font-size: 27px;
    font-weight: 400;
    letter-spacing: 1px;
  }
  .person-title {
    margin-top: 4px;
    font-size: 19px;
    color: var(--accent-orange);
    letter-spacing: 0.5px;
  }
  .person-title .jp {
    font-family: "Noto Serif JP", serif;
    font-size: 19px;
    margin-left: 4px;
  }
  .contacts {
    position: absolute;
    top: 300px;
    left: 0;
    right: 0;
    text-align: center;
    font-size: 18px;
    line-height: 1.7;
    letter-spacing: 0.5px;
  }
  .web-band {
    position: absolute;
    left: 0;
    right: 0;
    bottom: 0;
    height: 96px;
    background: var(--accent-orange);
    display: flex;
    align-items: center;
    justify-content: center;
    font-size: 20px;
    letter-spacing: 1px;
    color: var(--ink-white);
  }
  /* Back */
  .white-band {
    position: absolute;
    top: 0;
    bottom: 0;
    left: 110px;
    width: 130px;
    background: var(--card-white);
  }
  .back-title {
    position: absolute;
    top: 50%;
    left: 175px;
    transform: translate(-50%, -50%) rotate(90deg);
    white-space: nowrap;
    font-family: "Bodoni Moda", "Didot", serif;
    font-weight: 700;
    font-size: 40px;
    letter-spacing: 1px;
    color: var(--ink-black);
  }
</style>
</head>
<body>
<main class="stage">
  <section class="card card-front">
    <h1 class="brand-name">Torven Words</h1>
    <div class="person">
      <p class="person-name">Daniel Forsvik</p>
      <p class="person-title">Translator <span class="jp" lang="ja">翻訳者</span></p>
    </div>
    <div class="contacts">
      <p>twitter: @torven_wd</p>
      <p>dan.forsvik@quellmail.net</p>
    </div>
    <div class="web-band">www.torvenwords.com</div>
  </section>

  <section class="card card-back">
    <div class="white-band"></div>
    <p class="back-title">TORVEN WORDS</p>
  </section>
</main>
</body>
</html>
```